Software allocation system needs a business card design

We need a business card designed for our software platform - www.tallivo.com.au

At the moment the logo and website is all black and white, we are happy for suggestions on implementing some colour throughout either the logo or business card.

Industry/Entity Type

Software

Font styles to use
Sans Serif

Colors

Designer to choose colors to be used in the design.

```html
<!DOCTYPE html>
<html lang="en">
<head>
<meta charset="utf-8">
<title>Tallivo Business Card</title>
<link rel="stylesheet" href="https://fonts.googleapis.com/css2?family=Exo+2:wght@300;400;600&display=swap">
<style>
  :root {
    --backdrop: #e4e4e6;
    --card: #ffffff;
    --ink: #1e1e20;
    --ink-soft: #3a3a3d;
    --band-dark: #2b2b2e;
    --band-mid: #6d6d72;
    --band-light: #f2f2f2;
    --icon-bg: #232326;
    --icon-fg: #ffffff;
  }
  * { box-sizing: border-box; margin: 0; padding: 0; }
  html, body {
    width: 1200px; height: 937px; overflow: hidden;
    background: var(--backdrop);
    font-family: "Exo 2", sans-serif;
    color: var(--ink);
  }
  .card {
    position: absolute; left: 100px; top: 178px;
    width: 1000px; height: 580px;
    background: var(--card);
    box-shadow: 0 12px 40px rgba(0,0,0,0.18);
    overflow: hidden;
  }
  .side-band { position: absolute; left: 0; top: 0; width: 110px; height: 580px; }
  .brand {
    position: absolute; right: 70px; top: 52px;
    display: flex; align-items: center; gap: 22px;
  }
  .brand-dot { width: 46px; height: 46px; border-radius: 50%; background: var(--ink); }
  .brand-name {
    font-weight: 300; font-size: 92px; letter-spacing: 8px; line-height: 1;
    color: var(--ink);
  }
  .person { position: absolute; left: 130px; top: 270px; }
  .person-name { font-weight: 600; font-size: 34px; letter-spacing: 2px; text-transform: uppercase; }
  .person-role { font-weight: 400; font-size: 22px; margin-top: 4px; margin-left: 8px; color: var(--ink-soft); }
  .contacts { position: absolute; left: 150px; top: 390px; list-style: none; }
  .contacts li, .web {
    display: flex; align-items: center; gap: 22px;
    font-size: 22px; color: var(--ink-soft); height: 40px; margin-bottom: 20px;
  }
  .icon {
    width: 36px; height: 36px; background: var(--icon-bg);
    display: flex; align-items: center; justify-content: center; flex: none;
  }
  .icon svg { width: 20px; height: 20px; fill: var(--icon-fg); }
  .web { position: absolute; left: 560px; top: 296px; margin: 0; }
</style>
</head>
<body>
  <main class="card">
    <svg class="side-band" viewBox="0 0 110 580" aria-hidden="true">
      <rect width="110" height="580" fill="var(--band-dark)"/>
      <polygon points="0,0 110,0 110,110 0,330" fill="var(--band-mid)"/>
      <polygon points="110,110 110,150 0,370 0,330" fill="var(--band-light)"/>
    </svg>

    <div class="brand">
      <span class="brand-dot" aria-hidden="true"></span>
      <span class="brand-name">TALLIVO</span>
    </div>

    <section class="person">
      <h1 class="person-name">Daniel Whitford</h1>
      <p class="person-role">Managing Director</p>
    </section>

    <ul class="contacts">
      <li>
        <span class="icon"><svg viewBox="0 0 24 24"><path d="M12 2a7 7 0 0 0-7 7c0 5 7 13 7 13s7-8 7-13a7 7 0 0 0-7-7zm0 9.5A2.5 2.5 0 1 1 12 6.5a2.5 2.5 0 0 1 0 5z"/></svg></span>
        Harbour Street,48
      </li>
      <li>
        <span class="icon"><svg viewBox="0 0 24 24"><path d="M6.6 10.8a15 15 0 0 0 6.6 6.6l2.2-2.2a1 1 0 0 1 1-.25 11.4 11.4 0 0 0 3.6.57 1 1 0 0 1 1 1V20a1 1 0 0 1-1 1A17 17 0 0 1 3 4a1 1 0 0 1 1-1h3.5a1 1 0 0 1 1 1c0 1.25.2 2.45.57 3.57a1 1 0 0 1-.25 1z"/></svg></span>
        012 555 0142
      </li>
      <li>
        <span class="icon"><svg viewBox="0 0 24 24"><path d="M3 5h18v14H3zm2 2v.5l7 4.5 7-4.5V7zm0 2.9V17h14V9.9l-7 4.5z"/></svg></span>
        dan@tallivo.com
      </li>
    </ul>

    <p class="web">
      <span class="icon"><svg viewBox="0 0 24 24"><path d="M12 2a10 10 0 1 0 0 20 10 10 0 0 0 0-20zm6.9 6h-2.9a15 15 0 0 0-1.4-3.6A8 8 0 0 1 18.9 8zM12 4c.8 1.1 1.5 2.5 1.9 4h-3.8c.4-1.5 1.1-2.9 1.9-4zM4.3 14a8 8 0 0 1 0-4h3.3a16 16 0 0 0 0 4zm.8 2h2.9a15 15 0 0 0 1.4 3.6A8 8 0 0 1 5.1 16zM8 8H5.1a8 8 0 0 1 4.3-3.6A15 15 0 0 0 8 8zm4 12c-.8-1.1-1.5-2.5-1.9-4h3.8c-.4 1.5-1.1 2.9-1.9 4zm2.3-6H9.7a14 14 0 0 1 0-4h4.6a14 14 0 0 1 0 4zm.3 5.6A15 15 0 0 0 16 16h2.9a8 8 0 0 1-4.3 3.6zM16.4 14a16 16 0 0 0 0-4h3.3a8 8 0 0 1 0 4z"/></svg></span>
      www.tallivo.com.au
    </p>
  </main>
</body>
</html>
```